Business Cards for Internet Security Company

Awesome designers! This is the opportunity to help design cards for a forward thinking network security company. They use threat information gathered from peer groups to make intelligent decisions on what threats are relevant and which arent. ( not that you need this to do designs, but just so you know where they are coming from. ) :-)

We'd like to see a two side design and the deliverables will be in illustrator 4. The logo is attached and the logo colors are attached in the JPG and I've attached a an eps of the logo and icon

Security

```html
<!DOCTYPE html>
<html lang="en">
<head>
<meta charset="utf-8">
<title>Kelvane Business Card</title>
<link rel="stylesheet" href="https://fonts.googleapis.com/css2?family=Exo+2:wght@400;500;600&display=swap">
<style>
  :root {
    --ink: #1c1c1e;
    --brand-blue: #1f5fa8;
    --brand-blue-light: #3a9ae0;
    --brand-navy: #0f2f57;
    --paper: #f4f5f6;
    --paper-shade: #dfe2e5;
    --text-light: #f2f2f2;
    --backdrop: #e9e6e0;
  }
  * { margin: 0; padding: 0; box-sizing: border-box; }
  html, body { width: 1073px; height: 1200px; overflow: hidden; }
  body {
    background: var(--backdrop);
    font-family: "Exo 2", sans-serif;
    display: flex;
    align-items: center;
    justify-content: center;
    gap: 70px;
  }
  .card {
    position: relative;
    width: 420px;
    height: 735px;
    overflow: hidden;
    box-shadow: 0 12px 30px rgba(0,0,0,0.22);
  }
  .card-bg { position: absolute; inset: 0; }

  /* Front */
  .identity {
    position: absolute;
    top: 38px; right: 34px;
    text-align: right;
    color: var(--text-light);
  }
  .identity-name { font-size: 24px; font-weight: 600; letter-spacing: 2px; text-transform: uppercase; }
  .identity-role { font-size: 15px; letter-spacing: 0.5px; margin-top: 4px; }
  .contact-list {
    position: absolute;
    top: 120px; left: 60px; right: 34px;
    list-style: none;
    color: var(--text-light);
    text-align: center;
  }
  .contact-item { padding: 8px 0 10px; font-size: 15px; letter-spacing: 0.5px; }
  .contact-icon {
    display: flex; align-items: center; gap: 10px;
    justify-content: center;
    margin-bottom: 6px;
  }
  .contact-icon::before, .contact-icon::after {
    content: ""; flex: 0 0 90px; height: 1px; background: var(--text-light);
  }
  .contact-icon svg { width: 16px; height: 16px; fill: var(--text-light); }
  .address { line-height: 1.35; }

  .brand {
    position: absolute;
    display: flex; align-items: center; gap: 12px;
    color: var(--brand-blue);
    font-weight: 600;
    letter-spacing: 0.5px;
  }
  .brand-dot { border-radius: 50%; background: var(--brand-blue-light); flex: none; }
  .front .brand { left: 42px; bottom: 120px; font-size: 52px; }
  .front .brand-dot { width: 34px; height: 34px; }

  /* Back */
  .back .brand { left: 70px; top: 300px; font-size: 50px; }
  .back .brand-dot { width: 32px; height: 32px; }
  .back-website {
    position: absolute;
    left: 12px;
    bottom: 36px;
    writing-mode: vertical-rl;
    transform: rotate(180deg);
    color: var(--brand-navy);
    font-size: 16px;
    font-weight: 500;
    letter-spacing: 1px;
    white-space: nowrap;
  }
</style>
</head>
<body>

  <section class="card front" aria-label="Card front">
    <svg class="card-bg" viewBox="0 0 420 735" preserveAspectRatio="none" aria-hidden="true">
      <defs>
        <linearGradient id="paper-front" x1="0" y1="0" x2="1" y2="1">
          <stop offset="0" stop-color="#ffffff"/>
          <stop offset="1" stop-color="#e4e7ea"/>
        </linearGradient>
      </defs>
      <rect width="420" height="735" fill="url(#paper-front)"/>
      <polygon points="0,0 420,0 420,520 0,380" fill="var(--brand-blue)"/>
      <polygon points="0,0 420,0 420,500 0,360" fill="var(--ink)"/>
    </svg>

    <div class="identity">
      <p class="identity-name">Mara Tollen</p>
      <p class="identity-role">Chief Executive Officer &amp; Co-Founder</p>
    </div>

    <ul class="contact-list">
      <li class="contact-item">
        <span class="contact-icon"><svg viewBox="0 0 24 24"><path d="M6.6 10.8a15 15 0 0 0 6.6 6.6l2.2-2.2a1 1 0 0 1 1-.25 11.4 11.4 0 0 0 3.6.57 1 1 0 0 1 1 1V20a1 1 0 0 1-1 1A17 17 0 0 1 3 4a1 1 0 0 1 1-1h3.5a1 1 0 0 1 1 1c0 1.250.2 2.450.57 3.57a1 1 0 0 1-.25 1z"/></svg></span>
        012 555 0199
      </li>
      <li class="contact-item">
        <span class="contact-icon"><svg viewBox="0 0 24 24"><path d="M2 5h20v14H2z M2 5l10 8 10-8" fill="none" stroke="#f2f2f2" stroke-width="2"/></svg></span>
        hello@kelvane.com
      </li>
      <li class="contact-item">
        <span class="contact-icon"><svg viewBox="0 0 24 24"><circle cx="12" cy="12" r="9" fill="none" stroke="#f2f2f2" stroke-width="2"/><path d="M3 12h18M12 3c3 3 3 15 0 18M12 3c-3 3-3 15 0 18" fill="none" stroke="#f2f2f2" stroke-width="1.6"/></svg></span>
        www.kelvane.com
      </li>
      <li class="contact-item address">
        <span class="contact-icon"><svg viewBox="0 0 24 24"><path d="M12 2a7 7 0 0 0-7 7c0 5 7 13 7 13s7-8 7-13a7 7 0 0 0-7-7zm0 9.5A2.5 2.5 0 1 1 12 6.5a2.5 2.5 0 0 1 0 5z"/></svg></span>
        027 9th Floor Harbor Point<br>Road NW
      </li>
    </ul>

    <div class="brand"><span class="brand-dot"></span>Kelvane</div>
  </section>

  <section class="card back" aria-label="Card back">
    <svg class="card-bg" viewBox="0 0 420 735" preserveAspectRatio="none" aria-hidden="true">
      <defs>
        <linearGradient id="paper-back" x1="0" y1="0" x2="1" y2="1">
          <stop offset="0" stop-color="#ffffff"/>
          <stop offset="1" stop-color="#e2e5e8"/>
        </linearGradient>
        <linearGradient id="tab" x1="0" y1="0" x2="1" y2="1">
          <stop offset="0" stop-color="#5ab8f0"/>
          <stop offset="1" stop-color="#1f5fa8"/>
        </linearGradient>
      </defs>
      <rect width="420" height="735" fill="var(--ink)"/>
      <rect x="0" y="470" width="420" height="265" fill="var(--brand-blue)"/>
      <rect x="45" y="170" width="320" height="440" fill="var(--brand-blue)"/>
      <rect x="55" y="180" width="310" height="430" fill="url(#paper-back)"/>
      <rect x="290" y="460" width="110" height="190" fill="url(#tab)"/>
    </svg>

    <div class="brand"><span class="brand-dot"></span>Kelvane</div>
    <p class="back-website">www.kelvane.com</p>
  </section>

</body>
</html>
```